Business Card for Professional Photographer

I'm looking for an eye catching modern clean design that compliments my logo/ website fonts & colours.
I specialise in architecture, corporate & commercial photography so I'm marketing to professional clients rather than portrait / wedding clients.

I would prefer to not have a solid black design.

My logo brand guide is as follows :

Main front font. : Reislust
Main font colour : #fff
Slogan front font : Ubuntu Bold
Monogram front font : Venti Medium
Container colour : #fff

I need print ready files in pdf .png & .eps formats.

Included in the files below are some screen grabs as reference to font & colours etc.

```html
<!DOCTYPE html>
<html lang="en">
<head>
<meta charset="utf-8">
<title>True Line Studio – Business Card</title>
<link rel="stylesheet" href="https://fonts.googleapis.com/css2?family=Josefin+Sans:wght@300;400&family=Ubuntu:wght@400;700&family=Roboto:wght@400&display=swap">
<style>
  :root {
    --backdrop: #3a3a3c;
    --backdrop-edge: #1f1f21;
    --card-black: #1c1c1e;
    --card-black-2: #262628;
    --gold-light: #f3d889;
    --gold-mid: #d2a64a;
    --gold-deep: #a87a2a;
    --name-orange: #c9912f;
    --text-white: #f2f2f2;
    --text-dark: #1a1a1a;
  }
  * { margin: 0; padding: 0; box-sizing: border-box; }
  html, body { width: 799px; height: 1200px; overflow: hidden; }
  body {
    background: radial-gradient(ellipse at 50% 40%, var(--backdrop), var(--backdrop-edge));
    position: relative;
  }
  .card {
    position: absolute;
    left: 50px;
    width: 700px;
    height: 400px;
    border-radius: 4px;
    overflow: hidden;
    box-shadow: 0 18px 40px rgba(0,0,0,.55);
  }
  .card--front { top: 120px; background: var(--card-black); }
  .card--back  { top: 660px; background: linear-gradient(135deg, var(--card-black-2), var(--card-black)); }

  .gold-text {
    background: linear-gradient(90deg, var(--gold-deep), var(--gold-light) 50%, var(--gold-mid));
    -webkit-background-clip: text;
    background-clip: text;
    color: transparent;
  }

  /* front */
  .photo-collage {
    position: absolute; inset: 0;
    background: linear-gradient(120deg, #2a2f38 0%, #1e2126 40%, #2b2a28 70%, #1a1b1d 100%);
    opacity: .9;
  }
  .photo-shade { position: absolute; inset: 0; background: rgba(10,10,12,.45); }
  .front-brand {
    position: absolute; left: 80px; top: 120px;
    display: flex; align-items: center; gap: 22px;
  }
  .brand-dot {
    width: 44px; height: 44px; border-radius: 50%;
    background: linear-gradient(135deg, var(--gold-light), var(--gold-deep));
  }
  .brand-name {
    font-family: "Josefin Sans", sans-serif;
    font-weight: 300;
    font-size: 40px;
    letter-spacing: 5px;
    text-transform: uppercase;
  }
  .brand-slogan {
    font-family: "Ubuntu", sans-serif;
    font-weight: 700;
    font-size: 13px;
    letter-spacing: 2.6px;
    margin-top: 4px;
  }
  .front-web {
    position: absolute; left: 146px; top: 250px;
    font-family: "Josefin Sans", sans-serif;
    font-size: 20px; letter-spacing: 3px;
  }

  /* back */
  .back-brand { position: absolute; left: 60px; top: 110px; }
  .back-brand .brand-name { font-size: 31px; letter-spacing: 4px; }
  .back-brand .brand-slogan { font-size: 10.5px; letter-spacing: 2.2px; }
  .contact { position: absolute; left: 440px; top: 150px; font-family: "Roboto", sans-serif; }
  .contact-name {
    font-family: "Ubuntu", sans-serif; font-weight: 700;
    font-size: 21px; color: var(--name-orange);
  }
  .contact-role { font-size: 16px; color: var(--text-white); margin-top: 2px; }
  .contact-list { list-style: none; margin-top: 16px; }
  .contact-list li {
    display: flex; align-items: center; gap: 10px;
    font-size: 15px; color: var(--text-white); line-height: 23px;
  }
  .contact-icon { width: 13px; height: 13px; flex: none; }
  .gold-band { position: absolute; left: 0; bottom: 0; width: 700px; height: 110px; }
  .address {
    position: absolute; right: 40px; bottom: 22px;
    font-family: "Roboto", sans-serif; font-size: 17px; color: var(--text-dark);
  }
</style>
</head>
<body>

<section class="card card--front">
  <div class="photo-collage" role="img" aria-label="Collage of architecture and commercial photographs"></div>
  <div class="photo-shade"></div>
  <div class="front-brand">
    <span class="brand-dot"></span>
    <div>
      <div class="brand-name gold-text">True Line Studio</div>
      <div class="brand-slogan gold-text">Architecture Corporate Commercial</div>
    </div>
  </div>
  <div class="front-web gold-text">www.truelinestudio.com.au</div>
</section>

<section class="card card--back">
  <div class="back-brand">
    <div class="brand-name gold-text">True Line Studio</div>
    <div class="brand-slogan gold-text">Architecture Corporate Commercial</div>
  </div>

  <div class="contact">
    <div class="contact-name">Marcus Hale</div>
    <div class="contact-role">Photographer</div>
    <ul class="contact-list">
      <li>
        <svg class="contact-icon" viewBox="0 0 16 16"><path fill="#d2a64a" d="M3 1h3l1 4-2 1a9 9 0 0 0 5 5l1-2 4 1v3c0 1-1 2-2 2A13 13 0 0 1 1 3c0-1 1-2 2-2z"/></svg>
        0412555018
      </li>
      <li>
        <svg class="contact-icon" viewBox="0 0 16 16"><rect x="1" y="3" width="14" height="10" fill="#d2a64a"/><path d="M1 3l7 6 7-6" fill="none" stroke="#1c1c1e" stroke-width="1.2"/></svg>
        info@truelinestudio.com.au
      </li>
      <li>
        <svg class="contact-icon" viewBox="0 0 16 16"><circle cx="8" cy="8" r="7" fill="#d2a64a"/><path d="M1 8h14M8 1c-3 3-3 11 0 14M8 1c3 3 3 11 0 14" fill="none" stroke="#1c1c1e" stroke-width="1"/></svg>
        www.truelinestudio.com.au
      </li>
    </ul>
  </div>

  <svg class="gold-band" viewBox="0 0 700 110" preserveAspectRatio="none" aria-hidden="true">
    <defs>
      <linearGradient id="goldGrad" x1="0" y1="0" x2="1" y2="0">
        <stop offset="0" stop-color="#a87a2a"/>
        <stop offset=".45" stop-color="#f3d889"/>
        <stop offset="1" stop-color="#d2a64a"/>
      </linearGradient>
    </defs>
    <path d="M0 0 L310 40 Q318 24 338 24 L700 24 L700 110 L0 110 Z" fill="url(#goldGrad)"/>
    <path d="M0 10 L300 52 L0 52 Z" fill="#1c1c1e" opacity=".0"/>
  </svg>
  <div class="address">48 Harbour Rd Portland Vic 3305</div>
</section>

</body>
</html>
```